RW Holloway LLC Business Card - Civil Engineering & Consulting Firm

We need a Business Card that is elegant, and masculine.  It is our Professional Civil Engineering & Consulting Company located in San Antonio TX (Not s construction or builder firm- no gears & no tool images please). We provide civil engineering services including  commercial site plans, grading and drainage plans, utility plans, hydraulics and hydrology, land planning, utility coordination, and other general civil engineering services related to commercial and residential development.
We have 2 existing Logos. We would like to convey reliability, strength, trustworthiness and attention to detail.  Blues and orange tones as per logo We are OK with the use of a darker blue in the mix.  We have 2 logo versions - Full Company Name Logo to go on the back of card, & Small Icon Logo for the front w/ personal Info.

Target Market(s)
Architects, Real Estate Developers, Other Strctural Engineers, Surveyers, General Contractors
Industry/Entity Type
Professional Civil Engineering
Contact Information for Business Card
Name, Position, Address, Cell & Office #, email, and company website
Font styles to use
Other font styles liked:
- Avian
Requirements
Should not have
- No Tools, No Gears, no Cranes, or Construction Equipment.

```html
<!DOCTYPE html>
<html lang="en">
<head>
<meta charset="utf-8">
<title>RW Holloway LLC – Business Card</title>
<link rel="stylesheet" href="https://fonts.googleapis.com/css2?family=Questrial&family=Lato:wght@400&family=Roboto:wght@400&display=swap">
<style>
  :root {
    --backdrop: #9c9c9c;
    --paper: #ffffff;
    --brand-blue: #78acd9;
    --brand-orange: #ee8f2b;
    --ink: #1f1f1f;
    --rule: #8a8a8a;
  }
  * { box-sizing: border-box; margin: 0; padding: 0; }
  html, body { width: 1200px; height: 1200px; overflow: hidden; }
  body { background: var(--backdrop); position: relative; }

  .card { position: absolute; top: 303px; width: 369px; height: 593px; overflow: hidden; }

  /* Back of card */
  .card--back {
    left: 200px;
    background: linear-gradient(225deg, #ef8f2a 0%, #d39d64 28%, #a8a698 52%, #8eaccc 68%, var(--brand-blue) 82%);
  }
  .card--back .brand-name {
    position: absolute; left: 0; right: 0; top: 450px;
    text-align: center; color: #fff;
    font-family: "Questrial", sans-serif; font-size: 29px; letter-spacing: 3px;
    text-transform: uppercase;
  }

  /* Front of card */
  .card--front { left: 599px; background: var(--paper); text-align: center; }
  .front-brand {
    position: absolute; left: 0; right: 0; top: 140px;
    display: flex; justify-content: center; align-items: center; gap: 12px;
  }
  .front-brand .brand-mark { width: 22px; height: 22px; background: var(--brand-blue); }
  .front-brand .brand-name {
    font-family: "Questrial", sans-serif; font-size: 27px; letter-spacing: 2px;
    color: var(--brand-blue); text-transform: uppercase;
  }

  .person-name {
    position: absolute; left: 0; right: 0; top: 325px;
    font-family: "Questrial", sans-serif; font-size: 23px; letter-spacing: .5px;
    color: var(--brand-blue);
  }
  .person-name .surname { color: var(--brand-orange); }
  .person-title {
    position: absolute; left: 0; right: 0; top: 353px;
    font-family: "Roboto", sans-serif; font-size: 15px; color: var(--brand-orange);
  }

  .icon-row {
    position: absolute; left: 87px; width: 190px; top: 380px; height: 26px;
    display: flex; align-items: center; justify-content: center; gap: 4px;
  }
  .icon-row .rule { flex: 1; height: 1px; background: var(--rule); }
  .icon-row .rule:first-child { margin-right: 4px; }
  .icon-row .rule:last-child { margin-left: 4px; }
  .icon-row .icon { width: 25px; height: 25px; border-radius: 3px; background: var(--brand-blue); display: block; }

  .contact {
    position: absolute; left: 0; right: 0; top: 416px;
    font-family: "Lato", sans-serif; font-size: 17px; line-height: 22px; color: var(--ink);
  }
  .contact .highlight { color: var(--brand-orange); }
  .divider { position: absolute; left: 88px; width: 195px; top: 491px; height: 1px; background: var(--rule); }
  .address {
    position: absolute; left: 0; right: 0; top: 506px;
    font-family: "Lato", sans-serif; font-size: 17px; line-height: 22px; color: var(--ink);
  }
</style>
</head>
<body>
  <section class="card card--back" aria-label="Card back">
    <div class="brand-name">RW Holloway LLC</div>
  </section>

  <section class="card card--front" aria-label="Card front">
    <div class="front-brand">
      <span class="brand-mark"></span>
      <span class="brand-name">RW Holloway LLC</span>
    </div>

    <div class="person-name">DANIEL <span class="surname">MERCER</span></div>
    <div class="person-title">MANAGING DIRECTOR</div>

    <div class="icon-row">
      <span class="rule"></span>
      <svg class="icon" viewBox="0 0 25 25" aria-label="Phone">
        <rect width="25" height="25" rx="3" fill="#78acd9"/>
        <path d="M6 10c0-2 3-3 6.5-3S19 8 19 10l-2.5 1-1-2h-6l-1 2z" fill="#fff"/>
        <rect x="8" y="12" width="9" height="6" rx="1" fill="#fff"/>
      </svg>
      <svg class="icon" viewBox="0 0 25 25" aria-label="Email">
        <rect width="25" height="25" rx="3" fill="#78acd9"/>
        <rect x="6" y="8" width="13" height="9" fill="none" stroke="#fff" stroke-width="1.2"/>
        <path d="M6 8l6.5 5L19 8M6 17l5-4.5M19 17l-5-4.5" fill="none" stroke="#fff" stroke-width="1"/>
      </svg>
      <svg class="icon" viewBox="0 0 25 25" aria-label="Website">
        <rect width="25" height="25" rx="3" fill="#78acd9"/>
        <circle cx="12.5" cy="12.5" r="6.5" fill="#fff"/>
        <path d="M9.5 9.5c1.5-.5 2.5.5 2 2s-2 1-2.5 2.5M14 15c1-1 2.5-.5 2.5-2" fill="none" stroke="#78acd9" stroke-width="1.4"/>
      </svg>
      <span class="rule"></span>
    </div>

    <div class="contact">
      <div>044-987 654 321</div>
      <div>info@hollowayce.com</div>
      <div>www.<span class="highlight">hollowayce</span>.com</div>
    </div>
    <div class="divider"></div>
    <div class="address">
      <div>218, Brookline Avenue</div>
      <div>78205,Country Name</div>
    </div>
  </section>
</body>
</html>
```